quickdeedsale.com redesign with wireframes, white space and custom form are very important

Need a new two column design that will convert easily to mobile responsive. Lots of white space. Winning design will probably be based on header area and making the custom form stand out. I want the header to be very much like www.tallgatevk.com except the form not to go up into the header.
Here are some of the websites I really like:
www.birchdwell.com
http://ourplotpurchasedirect.com/
http://kellbrightproperty.com/

We buy homes for cash and close fast. Our target is a home seller who is desperate to sell quickly.
I have uploaded my really ugly wireframe and my logo. I also uploaded my photo for the about us box and a possible photo to use for the header.
The copy on the wireframe is what I will be using except for the about us box.

Here is the exact link for video to frame in the top left box.
https://clipvault.example/Qm38pzrtLa

0592cd
85cae6
eaf1f7
fbee3d
ec1f27

• Everything on wireframe.
• Must use Verdana font and nothing should be smaller than 12 point. Most should be in 14 point. (except maybe inside of form)

```html
<!DOCTYPE html>
<html lang="en">
<head>
<meta charset="utf-8">
<title>quickdeedsale.com – Sell Your Home For Cash</title>
<link rel="stylesheet" href="https://fonts.googleapis.com/css2?family=Noto+Sans:ital,wght@0,400;0,700;0,800;1,400;1,700&display=swap">
<style>
:root{
  --red:#ec1f27;--red-dark:#c3141b;--yellow:#fbee3d;--blue:#0592cd;--sky:#85cae6;--mist:#eaf1f7;
  --ink:#444;--text:#555;--muted:#777;--form:#e5d99b;--panel:#f5f5f5;--line:#e2e2e2;--foot:#1b1b1b;--foot-text:#b5b5b5;
}
*{box-sizing:border-box;margin:0;padding:0}
html,body{width:1200px;height:2744px;overflow:hidden;background:#fff}
body{font-family:Verdana,"Noto Sans",sans-serif;color:var(--text);font-size:16px;line-height:22px}
.page{position:relative;width:1200px;height:2744px}
.abs{position:absolute}

/* header */
.logo{left:100px;top:40px;display:flex;align-items:center;gap:10px;font-weight:700;font-size:26px;line-height:32px;color:var(--red)}
.logo .sq{width:22px;height:22px;background:var(--red)}
.call{right:98px;top:24px;font-size:24px;line-height:30px;color:var(--ink)}
.call b{color:var(--red);font-weight:400}
.nav{right:98px;top:88px;display:flex;gap:48px;font-size:16px;color:var(--ink)}
.hero{left:0;top:140px;width:1200px;height:338px;background:linear-gradient(180deg,#243f66 0%,#2a5fae 35%,#4d6e8a 70%,#6a6154 100%)}
.hero-title{left:0;top:222px;width:1200px;text-align:center;font-weight:800;font-size:42px;line-height:54px;color:#fff}
.hero-title .y{color:var(--yellow)}
.arrow{top:296px;width:24px;height:24px;border-left:2px solid rgba(255,255,255,.5);border-bottom:2px solid rgba(255,255,255,.5)}

/* columns */
.col{position:absolute;top:498px;display:flex;flex-direction:column}
.col-main{left:99px;width:541px;gap:14px}
.col-side{left:689px;width:411px;gap:15px}

/* left column */
h3.sec{font-size:22px;line-height:30px;font-weight:700;color:var(--ink)}
.ticks{list-style:none}
.ticks li{position:relative;padding-left:26px;font-size:16px;line-height:28px}
.ticks li::before{content:"";position:absolute;left:4px;top:6px;width:6px;height:12px;border-right:3px solid var(--red);border-bottom:3px solid var(--red);transform:rotate(40deg)}
.video{position:relative;height:242px;background:linear-gradient(180deg,#2c64b8 0%,#6e8fb5 45%,#d8d8d6 62%,#4e5a3c 100%)}
.play{position:absolute;left:241px;top:102px;width:58px;height:38px;background:var(--red);border-radius:8px}
.play::after{content:"";position:absolute;left:23px;top:11px;border-left:15px solid #fff;border-top:8px solid transparent;border-bottom:8px solid transparent}
.lead{font-size:19px;line-height:28px;color:var(--ink)}
.small{font-size:16px;line-height:22px;color:var(--muted)}
.blog{position:relative;border:1px solid var(--line);padding:14px 16px 16px;display:grid;grid-template-columns:170px 1fr;column-gap:18px}
.blog h4{grid-column:1 / 3;color:var(--red);font-size:18px;line-height:24px;font-weight:700;margin-bottom:12px}
.blog .thumb{height:132px}
.blog .name{font-size:16px;color:var(--ink)}
.blog .date{font-size:16px;color:var(--muted);margin:2px 0 4px}
.blog .txt{font-size:16px;line-height:22px;color:#666}
.links{border:1px solid var(--line);padding:12px 16px}

/* right column */
.form{background:var(--form);padding-bottom:18px}
.form-head{height:76px;background:var(--red);text-align:center;padding-top:12px}
.form-head h2{font-size:22px;line-height:28px;font-weight:700;color:var(--yellow)}
.form-head p{font-size:16px;line-height:22px;color:#fff;font-style:italic;margin-top:2px}
.fields{padding:16px 19px 0;display:flex;flex-direction:column;gap:8px}
.field{position:relative;height:32px;background:#fff;border-radius:3px;font-size:13px;line-height:16px;color:#999;padding:8px 11px}
.field.tall{height:70px}
.row{display:flex;gap:10px}
.sel::after{content:"";position:absolute;right:10px;top:14px;border:5px solid transparent;border-top-color:#777}
.submit{margin:0 18px;height:60px;background:var(--red);border-radius:3px;color:#fff;font-weight:700;font-size:17px;line-height:21px;text-align:center;padding-top:9px;box-shadow:0 3px 0 var(--red-dark)}
.shares{display:flex;gap:4px}
.share{height:29px;border-radius:3px;color:#fff;font-size:16px;line-height:29px;text-align:center;white-space:nowrap}
.callbox{background:linear-gradient(180deg,#1aa3dc,var(--blue));color:#fff;font-size:19px;line-height:27px;padding:13px 18px}
.panel{background:var(--panel);border:1px solid var(--line);padding:20px 21px}
.panel h5{font-size:18px;font-weight:700;color:var(--ink);line-height:25px;margin-bottom:10px}
.panel p{font-size:16px;line-height:22px;color:#666}

/* footer */
.footer{left:0;top:2460px;width:1200px;height:222px;background:var(--foot)}
.fh{font-size:18px;line-height:24px;color:#fff;top:2494px}
.fl{font-size:16px;line-height:24px;color:var(--foot-text);top:2530px}
.bottom{left:99px;top:2701px;font-size:16px;line-height:22px;color:#333}
.dot{top:2697px;width:30px;height:30px;border-radius:50%}
</style>
</head>
<body>
<div class="page">
  <div class="abs logo"><span class="sq"></span>quickdeedsale.com</div>
  <div class="abs call">Call us <b>407-555-0142</b></div>
  <nav class="abs nav"><span>SELL YOUR HOME</span><span>HOW IT WORKS</span><span>STOP FORECLOSURE</span><span>PROBATE</span><span>CONTACT</span></nav>

  <div class="abs hero" role="img" aria-label="Blurred photo of a suburban house under a blue sky"></div>
  <h1 class="abs hero-title"><span class="y">SELL YOUR HOME FOR CASH IN 8 DAYS</span><br>WE <i>BUY HOUSES</i> NATIONWIDE.</h1>
  <div class="abs arrow" style="left:30px;transform:rotate(45deg)"></div>
  <div class="abs arrow" style="right:30px;transform:rotate(-135deg)"></div>

  <main class="col col-main">
    <h3 class="sec">These are the benefits of selling your home to us.</h3>
    <ul class="ticks">
      <li>You pick the closing date</li><li>You pay NO commissions or fees</li><li>You don't have to paint, clean or make repairs</li>
    </ul>
    <p>Watch to see our president Dale explain how easy it is to sell to us.</p>
    <div class="video" role="img" aria-label="Video frame showing a white house with hedges"><span class="play"></span></div>
    <p class="lead">Sell your home or house fast for cash to a professional investor company. We buy Houses and close quickly.</p>
    <p class="small">Selling a home on your own has never been easier. From Orlando to Greensboro - and all points in between- you can sell your home today without any hassles. Call 1-800-555-0199 or fill out the form below to get a written offer on your home in just 36 hours. Sell today online to people that care.</p>

    <h3 class="sec" style="margin-top:8px">If you need to sell a home fast because of:</h3>
    <ul class="ticks">
      <li>Divorce or Bankruptcy</li><li>Foreclosure</li><li>Landlord problems - evictions with tenants okay</li><li>Inherited property in probate</li><li>Termites, mold, flood or fire damage, leaky roof</li><li>Moving or can't afford mortgage payments</li>
    </ul>
    <h3 class="sec">We Can Help. We are the fastest home buyers around.</h3>

    <article class="blog"><h4>Blog Entry 1</h4><div class="thumb" role="img" aria-label="Photo of red brick townhouses" style="background:linear-gradient(180deg,#5b9ad8,#b45a3c 55%,#5e8a3a)"></div><div><div class="name">Blog Name1</div><div class="date">Wednesday, May 05</div><p class="txt">Lorem ipsum dolor sit amet, consectetur adiiscing elit, sed do eiusmod tempor incidi dunt ut labore et dolore magna aliquanim ad minim veniam, quis nostrud exercitation</p></div></article>
    <article class="blog"><h4>Blog Entry 2</h4><div class="thumb" role="img" aria-label="Photo of a stucco house with a car in the driveway" style="background:linear-gradient(180deg,#3a7fd0,#c9a074 55%,#6d6d6d)"></div><div><div class="name">Blog Name 2</div><div class="date">Wednesday, May 05</div><p class="txt">Lorem ipsum dolor sit amet, consectetur adiiscing elit, sed do eiusmod tempor incidi dunt ut labore et dolore magna aliquanim ad minim veniam, quis nostrud exercitation</p></div></article>
    <article class="blog"><h4>Blog Entry 3</h4><div class="thumb" role="img" aria-label="Photo of a small blue boarded-up house" style="background:linear-gradient(180deg,#6fa0d6,#3e6fa8 55%,#4e7a36)"></div><div><div class="name">Blog Name 3</div><div class="date">Wednesday, May 05</div><p class="txt">Lorem ipsum dolor sit amet, consectetur adiiscing elit, sed do eiusmod tempor incidi dunt ut labore et dolore magna aliquanim ad minim veniam, quis nostrud exercitation</p></div></article>

    <ul class="links ticks"><li>Archives</li><li>Sell my house</li><li>Fast cash for homes</li><li>We buy houses</li><li>Real Estate investor</li><li>Latest</li></ul>
  </main>

  <aside class="col col-side">
    <form class="form">
      <div class="form-head"><h2>Yes, I want to sell my home fast!</h2><p>Get a no obligation written offer in 36 hours</p></div>
      <div class="fields">
        <div class="field">Your Name</div>
        <div class="field">Your phone number</div>
        <div class="field">Your Email Address</div>
        <div class="field tall">Property Address</div>
        <div class="row"><div class="field sel" style="width:97px">City</div><div class="field sel" style="width:156px">State</div><div class="field sel" style="width:100px">Zip Code</div></div>
        <div class="field">Repairs needed if any</div>
        <div class="field">Asking price</div>
        <div class="field tall" style="margin-bottom:12px">Comments</div>
      </div>
      <div class="submit">Submit, to get started selling your<br>home fast.</div>
    </form>

    <div class="shares">
      <div class="share" style="width:155px;background:var(--red)">Our Privacy Policy</div>
      <div class="share" style="width:82px;background:#333">Share 159</div>
      <div class="share" style="width:82px;background:#2b4d8f">Share 154</div>
      <div class="share" style="width:80px;background:#33aef0">Share 147</div>
    </div>

    <div class="callbox">Call us 8am to 10 pm Eastern time.<br>We answer our phones.</div>

    <section class="panel">
      <h5>Home Seller Testimonials</h5>
      <p style="font-style:italic">" I just wanted to thank you for buying my home in Winter Park. You made it fast and easy and kept me well informed the whole way."</p>
      <p style="color:var(--blue);margin-top:8px">Corwin Hale – Winter Park</p>
      <p style="color:var(--red);text-align:right">More Testimonials</p>
    </section>

    <section class="panel">
      <h5>About Us</h5>
      <p>Owned and operated in Orlando Florida since 2001. Oldest Continuous operated website in country.</p>
      <div role="img" aria-label="Portrait photo of the company president" style="width:96px;height:100px;margin-top:10px;background:linear-gradient(180deg,#4f7fb0,#c9a488)"></div>
    </section>

    <section class="panel">
      <h5>Some of the cities where we buy houses. Not all are listed.</h5>
      <p>These are the cities where we have an affiliate where you can sell a home fast or quickly and we buy homes: Orlando Jacksonville Ft Myers Tampa St Pete Gainesville Tallahassee Melbourne West Palm Beach Apopka Deland Kissimmee Lakeland Ocala Chicago Philadelphia Camden Atlanta Valdosta Houston Detroit Phoenix Seattle Tacoma Portland Charlotte Cincinnati San Antonio Harrisburg Virginia Beach Virginia Homes Greensboro Charleston SC Flint Rochester Lake Florida Wilmington Columbia Titusville If you don't see your city, we still probably buy homes there.</p>
      <p style="margin-top:14px">These are the types of real estate that we buy: We buy nice houses and outdated problem homes. We buy in great neighborhoods and not so nice. We buy block homes and frame homes. We buy</p>
    </section>

    <section class="panel" style="padding:12px">
      <div style="display:flex;gap:14px">
        <div role="img" aria-label="Photo of a tidy white house with a lawn" style="width:186px;height:106px;background:linear-gradient(180deg,#9fb9d2,#e8e8e4 50%,#4f7a3a)"></div>
        <div role="img" aria-label="Photo of a plain single-storey house" style="width:186px;height:106px;background:linear-gradient(180deg,#b9cce0,#2e2e2e 55%,#6c8a4a)"></div>
      </div>
      <p style="color:var(--red);text-align:center;margin-top:8px">We buy nice pretty houses and some ugly ones as well</p>
    </section>
  </aside>

  <footer class="abs footer"></footer>
  <div class="abs fh" style="left:99px">Our Services</div>
  <div class="abs fl" style="left:99px">We buy Houses '<br>Sell home today online<br>Sell house fast on net<br>Cash home buyer company<br>Links</div>
  <div class="abs fl" style="left:340px">Quickly sell your home<br>Fastest web home buyer people<br>For Investors</div>
  <div class="abs fh" style="left:640px">Contact Us</div>
  <div class="abs fl" style="left:640px">2240 Marigold Ave #310<br>Winter Park, FL 32789<br>407-555-0142<br>1-800-555-0199<br>hello@quickdeedsale.com</div>
  <div class="abs fh" style="left:898px">Newsletter</div>
  <div class="abs" style="left:898px;top:2532px;width:203px;height:36px;background:#e6e6e6;font-size:14px;line-height:16px;color:#777;padding:10px">Enter Email Address</div>
  <div class="abs" style="left:898px;top:2580px;width:96px;height:40px;background:var(--red);color:#fff;font-size:16px;line-height:40px;text-align:center">SUBMIT</div>

  <div class="abs bottom">© Copyright all rights reserved &nbsp;| &nbsp;Privacy Policy . Administration | Agent County Property</div>
  <div class="abs dot" style="left:988px;background:#2b4d8f"></div>
  <div class="abs dot" style="left:1026px;background:#33aef0"></div>
  <div class="abs dot" style="left:1064px;background:var(--red)"></div>
  <div class="abs bottom" style="left:1148px;color:#555">C4</div>
</div>
</body>
</html>
```